Real Estate Brokerage Stationery Designs

I am looking to have presentation folders with business card slots on both sides along with pockets on both sides. I've attached logos, website colors along with current business card designs.

I am looking for envelope designs both big and small. Possibly new business card designs, notepad templates for big and small notepads. Letterhead designs. Pop socket designs. Realtors name badge designs.

www.brightholdrealty.example

```html
<!DOCTYPE html>
<html lang="en">
<head>
<meta charset="utf-8">
<title>Brighthold Realty Stationery</title>
<link href="https://fonts.googleapis.com/css2?family=Open+Sans:wght@400;600&family=Tinos&display=swap" rel="stylesheet">
<style>
:root{
  --stage:#a9a8a9;
  --paper-light:#f6f6f6;
  --paper-dark:#dedede;
  --brand-blue:#0057a6;
  --band-grey:#b3b3b3;
  --ink:#444;
  --ink-soft:#555;
}
*{box-sizing:border-box;margin:0;padding:0}
html,body{width:1200px;height:871px;overflow:hidden;background:var(--stage)}
.canvas{position:relative;width:1200px;height:871px}
.sheet{position:absolute;background:linear-gradient(90deg,var(--paper-light),var(--paper-dark));box-shadow:0 1px 3px rgba(0,0,0,.35)}
.envelope-front{left:54px;top:216px;width:560px;height:255px}
.envelope-back{left:54px;top:500px;width:560px;height:254px;overflow:hidden}
.letterhead{left:638px;top:57px;width:522px;height:735px}
.footer-band{position:absolute;left:0;bottom:0;width:100%;height:22px}
.footer-url{position:absolute;bottom:5px;right:12px;font:600 7px/1 "Open Sans",sans-serif;letter-spacing:2.4px;color:#fff}
.brand{position:absolute;display:flex;align-items:center;gap:6px;font:600 15px/1 "Open Sans",sans-serif;color:var(--brand-blue)}
.brand-square{width:12px;height:12px;background:var(--brand-blue)}
.envelope-front .brand{left:34px;top:104px}
.envelope-address{position:absolute;left:20px;top:128px;width:130px;text-align:center;font:400 7px/9.5px "Open Sans",sans-serif;color:var(--ink)}
.flap{position:absolute;left:0;top:0;width:560px;height:95px}
.flap-name{position:absolute;left:0;top:42px;width:560px;text-align:center;font:600 14px/1 "Open Sans",sans-serif;color:#fff}
.letterhead .brand{left:46px;top:128px}
.contact{position:absolute;left:375px;top:72px;font:400 6.8px/10px "Open Sans",sans-serif;color:var(--ink)}
.contact-list{list-style:none;margin-top:5px}
.contact-list li{display:flex;align-items:center;gap:5px;line-height:10.2px}
.contact-list svg{width:7px;height:7px;fill:var(--brand-blue)}
.letter{position:absolute;left:49px;top:180px;width:431px;font:400 8.6px/12px "Tinos",serif;color:var(--ink-soft)}
.letter-date{margin-bottom:24px;font-size:9px}
.recipient{margin-bottom:24px;font-size:9px}
.letter p{text-align:justify;margin-bottom:12px}
.signature{position:absolute;left:52px;top:527px;width:106px;height:44px;background:linear-gradient(90deg,#d9d9d9,#cfcfcf);border-radius:4px}
</style>
</head>
<body>
<main class="canvas">

  <section class="sheet envelope-front" aria-label="Envelope front">
    <div class="brand"><span class="brand-square"></span>Brighthold Realty</div>
    <p class="envelope-address">2400 Harbor Lane, Suite 310,<br>Cedar Point, FL 33000</p>
    <svg class="footer-band" viewBox="0 0 560 22" preserveAspectRatio="none">
      <rect x="0" y="12" width="560" height="10" fill="var(--band-grey)"/>
      <polygon points="394,22 414,3 560,3 560,22" fill="var(--brand-blue)"/>
    </svg>
    <span class="footer-url">www.brightholdrealty.example</span>
  </section>

  <section class="sheet envelope-back" aria-label="Envelope back">
    <svg class="flap" viewBox="0 0 560 95">
      <path d="M0 0 H560 L550 55 Q543 94 505 94 H55 Q17 94 10 55 Z" fill="var(--brand-blue)"/>
    </svg>
    <div class="flap-name">Brighthold Realty</div>
  </section>

  <section class="sheet letterhead" aria-label="Letterhead">
    <div class="brand"><span class="brand-square"></span>Brighthold Realty</div>

    <address class="contact" style="font-style:normal">
      2400 Harbor Lane, Suite 310,<br>Cedar Point, FL 33000
      <ul class="contact-list">
        <li><svg viewBox="0 0 10 10"><path d="M1 3 Q5 0 9 3 L8 5 H6.5 L6 4 H4 L3.5 5 H2 Z M2 6 H8 V9 H2 Z"/></svg>555-201-4410</li>
        <li><svg viewBox="0 0 10 10"><path d="M2.5 0 H7.5 V10 H2.5 Z M3.5 1.2 V7.5 H6.5 V1.2 Z"/></svg>555-201-4411</li>
        <li><svg viewBox="0 0 10 10"><path d="M1 4 H9 V9 H1 Z M3 1 H7 V4 H3 Z"/></svg>555-201-4412</li>
        <li><svg viewBox="0 0 10 10"><path d="M0.5 2.5 H9.5 V8 H0.5 Z"/></svg>hello@brightholdrealty.example</li>
      </ul>
    </address>

    <article class="letter">
      <p class="letter-date">Cartagena de Indias, Ocober 12,2015</p>
      <div class="recipient">Sr.<br>MARCO RUIZ<br>Web Master<br>City</div>
      <p>Contrary to popular belief, Lorem Ipsum is not simply random text. It has roots in a piece of classical Latin literature from 45 BC, making it over 2000 years old. Daniel Marsh, a Latin professor at Linden Hill College in Ohio, looked up one of the more obscure Latin words, consectetur, from a Lorem Ipsum passage, and going through the cites of the word in classical literature,</p>
      <p>discovered the undoubtable source. Lorem Ipsum comes from sections 1.10.32 and 1.10.33 of "de Finibus Bonorum et Malorum" (The Extremes of Good and Evil) by Cicero, written in 45 BC. This book is a treatise on the theory of ethics, very popular during the Renaissance. The first line of Lorem Ipsum, "Lorem ipsum dolor sit amet..", comes from a line in section 1.10.32.</p>
      <p>The standard chunk of Lorem Ipsum used since the 1500s is reproduced below for those interested. Sections 1.10.32 and 1.10.33 from "de Finibus Bonorum et Malorum" by Cicero are also reproduced in their exact original form, accompanied by English versions from the 1914 translation by H. Lowell.</p>
      <p>There are many variations of passages of Lorem Ipsum available, but the majority have suffered alteration in some form, by injected humour, or randomised words which don't look even slightly believable. If you are going to use a passage of Lorem Ipsum, you need to be sure there isn't anything embarrassing hidden in the middle of text.</p>
    </article>

    <div class="signature" role="img" aria-label="Handwritten signature"></div>

    <svg class="footer-band" viewBox="0 0 522 22" preserveAspectRatio="none">
      <rect x="0" y="12" width="522" height="10" fill="var(--band-grey)"/>
      <polygon points="356,22 376,2 522,2 522,22" fill="var(--brand-blue)"/>
    </svg>
    <span class="footer-url">www.brightholdrealty.example</span>
  </section>

</main>
</body>
</html>
```